International Clinical Software Company needs a new business card design

We are looking for a new business card design for our company that has recently expanded into the UK market, making us a multinational company.
After having rebranded our website and produced a new style guide, we are looking for a business card that is creative and attention grabbing, while being consistent with the style and colour scheme used on the new website, www.plumvora.example
We produce care management technology for the aged care market, but the main aspect we aim to communicate is the human element of our software, and the way it assists in providing better care for aged people, and stronger relationships between aged people and the staff that care for them.
Our current business card is a dark green with gold text, which makes the text quite difficult to read, not very aesthetically appealing and the colour scheme looks quite dated.
We would like something fresh and modern, that can still be colourful but doesn't use large blocks of dark colour, and uses the colours within our logo.
Something tying in with the leaves that are used in our logo could work quite nicely, along with the Autumn/Fall colours of soft greens, yellows and reds (also in our existing logo). However also happy to look at fresh, completely out of the box ideas we may not have yet considered.
Target Market(s)
The people that receive this business card work in the aged card or health industry and are either corporate/management level staff or clinical (Registered Nurses, care workers etc.)
Industry/Entity Type
Health Product
Contact Information for Business Card
Company Name - BrindlewayCare
Company locations: United Kingdom, Australia, New Zealand
Staff Details:
Staff name: Derek Mallow
Staff job title: Executive Chairman
Staff email: d.mallow@plumvora.example
Office phone number: 01742 918576
Font styles to use
Other font styles liked:
- Calibri
Requirements
Must have
- Must include the BrindlewayCare brand name in it's current font
- Must include logo (3 leaves in gold circle)
- Must include Business Card Details
Nice to have
- Elements of gold
- White space
- Something autumn themed but not too cliched
Should not have
- No blue - used by a major competitor and we would like to differentiate from them
- Large blocks of dark green colour (the green that appears in our leaves on the logo on our current business card is the background colour and it is far too dark)

```html
<!DOCTYPE html>
<html lang="en">
<head>
<meta charset="utf-8">
<title>BrindlewayCare Business Card</title>
<link rel="stylesheet" href="https://fonts.googleapis.com/css2?family=Source+Sans+3:wght@400;600&display=swap">
<style>
  :root {
    --stage-top: #1e1e1e;
    --stage-bottom: #050505;
    --card-paper: #fbfaf6;
    --card-paper-edge: #f1eee4;
    --gold: #a08448;
    --ink: #4a4a4a;
    --leaf-yellow: #e9cd2b;
    --leaf-orange: #e58b2b;
    --leaf-red: #cf4b3c;
    --leaf-brown: #6e2c17;
    --leaf-green: #7d8c2f;
  }
  * { margin: 0; padding: 0; box-sizing: border-box; }
  html, body {
    width: 1200px; height: 900px; overflow: hidden;
  }
  body {
    background: linear-gradient(to bottom, var(--stage-top), var(--stage-bottom));
    font-family: "Source Sans 3", "Calibri", sans-serif;
    position: relative;
  }
  .card {
    position: absolute;
    top: 306px;
    width: 440px;
    height: 271px;
    background: radial-gradient(ellipse at 45% 55%, #ffffff 0%, var(--card-paper) 55%, var(--card-paper-edge) 100%);
    overflow: hidden;
  }
  .card--front { left: 149px; }
  .card--back { left: 608px; }
  .leaf-spray {
    position: absolute; inset: 0; width: 100%; height: 100%;
  }
  .contact {
    position: absolute; left: 24px; top: 25px;
  }
  .contact__name {
    color: var(--gold); font-weight: 600; font-size: 15px; line-height: 17px;
  }
  .contact__title {
    color: var(--ink); font-size: 12px; line-height: 15px;
  }
  .contact__email {
    margin-top: 13px; color: var(--ink); font-size: 12px;
    display: flex; align-items: center; gap: 6px;
  }
  .contact__icon { width: 9px; height: 9px; fill: var(--gold); }
  .locations {
    position: absolute; right: 20px; top: 227px;
    text-align: right; color: var(--ink); font-size: 12.5px; line-height: 15px;
  }
  .brand {
    position: absolute; right: 16px; top: 19px;
    display: flex; align-items: center; gap: 6px;
  }
  .brand__mark {
    width: 58px; height: 58px; border-radius: 50%;
    border: 2px solid var(--gold);
  }
  .brand__name {
    color: var(--gold); font-size: 22px; font-weight: 400; letter-spacing: 0.2px;
  }
</style>
</head>
<body>

<section class="card card--front">
  <svg class="leaf-spray" viewBox="0 0 440 271" role="img" aria-label="Illustrated spray of autumn leaves arcing from the lower left corner to the upper right">
    <defs>
      <linearGradient id="autumnFront" x1="0" y1="1" x2="1" y2="0">
        <stop offset="0" stop-color="var(--leaf-red)"/>
        <stop offset="0.25" stop-color="var(--leaf-orange)"/>
        <stop offset="0.5" stop-color="var(--leaf-red)"/>
        <stop offset="0.7" stop-color="var(--leaf-brown)"/>
        <stop offset="0.85" stop-color="var(--leaf-yellow)"/>
        <stop offset="1" stop-color="var(--leaf-green)"/>
      </linearGradient>
    </defs>
    <path fill="url(#autumnFront)" opacity="0.85"
      d="M0,205 C60,150 130,105 200,55 C250,25 300,5 340,0 L440,0 L440,190 C400,175 360,170 320,180 C260,190 190,200 140,220 C100,235 70,255 55,271 L0,271 Z"/>
  </svg>
  <div class="contact">
    <p class="contact__name">Derek Mallow</p>
    <p class="contact__title">Executive Chairman</p>
    <p class="contact__email">
      <svg class="contact__icon" viewBox="0 0 10 10" aria-hidden="true"><path d="M2,0.5 L3.6,2.6 L2.6,3.7 C3.2,5 4.8,6.8 6.3,7.4 L7.4,6.4 L9.5,8 L8.5,9.5 C4.5,9.5 0.5,5.5 0.5,1.5 Z"/></svg>
      d.mallow@plumvora.example
    </p>
  </div>
  <p class="locations">United Kingdom, Australia<br>New Zealand</p>
</section>

<section class="card card--back">
  <svg class="leaf-spray" viewBox="0 0 440 271" role="img" aria-label="Illustrated spray of autumn leaves arcing from the upper left to the lower right corner">
    <defs>
      <linearGradient id="autumnBack" x1="0" y1="1" x2="1" y2="0">
        <stop offset="0" stop-color="var(--leaf-red)"/>
        <stop offset="0.25" stop-color="var(--leaf-orange)"/>
        <stop offset="0.5" stop-color="var(--leaf-red)"/>
        <stop offset="0.7" stop-color="var(--leaf-brown)"/>
        <stop offset="0.85" stop-color="var(--leaf-yellow)"/>
        <stop offset="1" stop-color="var(--leaf-green)"/>
      </linearGradient>
    </defs>
    <g transform="translate(440,0) scale(-1,1)">
      <path fill="url(#autumnBack)" opacity="0.85"
        d="M0,205 C60,150 130,105 200,55 C250,25 300,5 340,0 L440,0 L440,190 C400,175 360,170 320,180 C260,190 190,200 140,220 C100,235 70,255 55,271 L0,271 Z"/>
    </g>
  </svg>
  <div class="brand">
    <span class="brand__mark" aria-hidden="true"></span>
    <span class="brand__name">BrindlewayCare</span>
  </div>
</section>

</body>
</html>
```